Corporate Business Card

Very professional, Modern, Not to busy, include phone address email, website
(253) 617-4930, 18761 52nd Avenue S, Kent, WA 98047, martin@plumlinegroup.com, varkoworks.com

Target Market(s)

Manufacturing

Industry/Entity Type

Aero, machining, manufacturing, Off road racing

Contact Information for Business Card

Phone, address email, website

```html
<!DOCTYPE html>
<html lang="en">
<head>
<meta charset="utf-8">
<title>Varko Works – Business Card</title>
<link rel="stylesheet" href="https://fonts.googleapis.com/css2?family=Roboto:wght@400;500;700&family=Orbitron:wght@700&display=swap">
<style>
  :root {
    --navy: #2a3a68;
    --navy-deep: #24335e;
    --red: #c0232a;
    --paper: #efefef;
    --paper-shade: #e4e4e4;
    --stage: #2c2c2c;
    --ink: #1f2a4d;
    --white: #ffffff;
  }
  * { margin: 0; padding: 0; box-sizing: border-box; }
  html, body {
    width: 1200px;
    height: 1138px;
    overflow: hidden;
    background: var(--stage);
    font-family: "Roboto", Arial, sans-serif;
  }
  .card {
    position: absolute;
    border-radius: 14px;
    overflow: hidden;
    background: linear-gradient(160deg, #f5f5f5 0%, var(--paper) 55%, var(--paper-shade) 100%);
  }
  .card--front { left: 274px; top: 186px; width: 623px; height: 376px; }
  .card--back  { left: 276px; top: 608px; width: 618px; height: 374px; }

  /* Front */
  .front-mark {
    position: absolute;
    left: 0; right: 0; top: 112px;
    text-align: center;
  }
  .front-mark__name {
    font-weight: 700;
    font-size: 66px;
    letter-spacing: 2px;
    color: var(--navy);
    line-height: 1;
  }
  .front-mark__rule {
    width: 196px;
    height: 2px;
    background: var(--navy);
    margin: 26px auto 0;
  }
  .front-web {
    position: absolute;
    left: 0; right: 0; top: 328px;
    display: flex;
    justify-content: center;
    align-items: center;
    gap: 18px;
    font-size: 16px;
    color: #222;
  }
  .front-web__dash {
    width: 72px;
    height: 3px;
    background: linear-gradient(90deg, transparent, var(--red) 30%, var(--red) 70%, transparent);
    border-radius: 2px;
  }
  .front-band {
    position: absolute;
    left: 0; right: 0; bottom: 0;
    height: 10px;
    display: flex;
  }
  .front-band__navy { flex: 1; background: var(--navy); }
  .front-band__red  { flex: 1; background: var(--red); }

  /* Back */
  .back-panel {
    position: absolute;
    left: 0; top: 0;
    width: 320px; height: 374px;
  }
  .back-mark {
    position: absolute;
    left: 24px; width: 240px; top: 150px;
    text-align: center;
  }
  .back-mark__name {
    font-weight: 700;
    font-size: 34px;
    letter-spacing: 1px;
    color: var(--white);
    line-height: 1;
  }
  .back-mark__rule {
    width: 112px;
    height: 2px;
    background: var(--white);
    margin: 16px auto 0;
  }
  .contact {
    position: absolute;
    left: 336px; top: 108px;
    color: var(--ink);
  }
  .contact__name {
    font-family: "Orbitron", "Roboto", sans-serif;
    font-weight: 700;
    font-size: 22px;
    letter-spacing: 0.5px;
    color: var(--navy);
    margin-bottom: 14px;
  }
  .contact__list { list-style: none; }
  .contact__item {
    position: relative;
    padding-left: 32px;
    font-size: 16.5px;
    line-height: 24px;
  }
  .contact__icon {
    position: absolute;
    left: 0; top: 5px;
    width: 14px; height: 14px;
    fill: var(--red);
  }
</style>
</head>
<body>

<section class="card card--front" aria-label="Card front">
  <div class="front-mark">
    <div class="front-mark__name">VARKO WORKS</div>
    <div class="front-mark__rule"></div>
  </div>
  <div class="front-web">
    <span class="front-web__dash"></span>
    <span>www.varkoworks.com</span>
    <span class="front-web__dash"></span>
  </div>
  <div class="front-band">
    <span class="front-band__navy"></span>
    <span class="front-band__red"></span>
  </div>
</section>

<section class="card card--back" aria-label="Card back">
  <svg class="back-panel" viewBox="0 0 320 374" aria-hidden="true">
    <path d="M0 0 H262 Q336 187 258 374 H0 Z" fill="var(--red)"/>
    <path d="M0 0 H252 Q324 187 248 374 H0 Z" fill="var(--navy)"/>
  </svg>
  <div class="back-mark">
    <div class="back-mark__name">VARKO WORKS</div>
    <div class="back-mark__rule"></div>
  </div>

  <div class="contact">
    <h1 class="contact__name">MARTIN KOVAC</h1>
    <ul class="contact__list">
      <li class="contact__item">
        <svg class="contact__icon" viewBox="0 0 16 16"><path d="M1 6c0-2 3-4 7-4s7 2 7 4v1h-4V5.5H5V7H1z M3 8h10l1 6H2z"/></svg>
        (253) 617-4930
      </li>
      <li class="contact__item">
        <svg class="contact__icon" viewBox="0 0 16 16"><path d="M1 3h14v10H1z M2 4.2v1L8 9l6-3.8v-1L8 8z" fill-rule="evenodd"/></svg>
        martin@plumlinegroup.com
      </li>
      <li class="contact__item">
        <svg class="contact__icon" viewBox="0 0 16 16"><path d="M8 1a5 5 0 0 1 5 5c0 4-5 9-5 9S3 10 3 6a5 5 0 0 1 5-5zm0 3a2 2 0 1 0 0 4 2 2 0 0 0 0-4z" fill-rule="evenodd"/></svg>
        18761 52nd Avenue S,<br>Kent, WA 98047
      </li>
      <li class="contact__item">
        <svg class="contact__icon" viewBox="0 0 16 16"><path d="M8 1a7 7 0 1 1 0 14A7 7 0 0 1 8 1zm-1 1.6C5.8 4 5.2 5.8 5.1 7.3h1.9V2.6zm2 0v4.7h1.9C10.8 5.8 10.2 4 9 2.6zM2.6 8.7c.3 2 1.7 3.7 3.6 4.4-.7-1.2-1.1-2.7-1.1-4.4zm8.3 0c0 1.7-.4 3.2-1.1 4.4 1.9-.7 3.3-2.4 3.6-4.4zM7 8.7H5.1c.1 1.6.7 3.4 1.9 4.7zm2 0v4.7c1.2-1.3 1.8-3.1 1.9-4.7zM2.6 7.3h2.5c0-1.7.4-3.2 1.1-4.4-1.9.7-3.3 2.4-3.6 4.4zm8.3 0h2.5c-.3-2-1.7-3.7-3.6-4.4.7 1.2 1.1 2.7 1.1 4.4z"/></svg>
        www.varkoworks.com
      </li>
    </ul>
  </div>
</section>

</body>
</html>
```